Design a "healthy, happy dog and cat" cheque/check background

I am looking for a few design concepts featuring a happy healthy dog and cat, that will be used as the background of a paper cheque/check.

This will require Photoshop and stock photos.

Here is the design brief: https://docs.plinvaro.com/document/d/4Rt8mKx2LqW9zVbN3cHy7TfJ1sDp6GaE0uYoZiXeMwnB/edit?usp=sharing

Colors

Designer to choose colors to be used in the design.

Requirements
Must have
• A happy dog and cat the main focus within the "empty" central part of the cheque/check, and a complementary background for the rest of the cheque, following the design guidelines in the attached plinvaro doc.

```html
<!DOCTYPE html>
<html lang="en">
<head>
<meta charset="utf-8">
<title>Personal Cheque – Dog and Cat</title>
<link rel="stylesheet" href="https://fonts.googleapis.com/css2?family=Arimo:wght@400;700&family=Share+Tech+Mono&display=swap">
<style>
  :root {
    --page: #ffffff;
    --tan: #d2af8c;
    --tan-light: #dcbf9f;
    --ink: #1e1a16;
    --ink-soft: #3a332c;
    --line: #4a4038;
    --field: #ffffff;
    --fur-gold: #e9c48c;
    --fur-cream: #f1dcbc;
    --fur-grey: #cfc7c0;
    --fur-grey-dark: #b9afa6;
  }
  * { margin: 0; padding: 0; box-sizing: border-box; }
  html, body {
    width: 1200px; height: 544px; overflow: hidden;
    background: var(--page);
    font-family: "Arimo", Arial, sans-serif;
    color: var(--ink);
  }
  .canvas { position: relative; width: 1200px; height: 544px; }
  .abs { position: absolute; }
  .cheque {
    left: 24px; top: 20px; width: 1172px; height: 395px;
    background: var(--tan);
  }
  .pet-photo {
    left: 185px; top: 20px; width: 685px; height: 395px;
    border-radius: 220px 260px 0 0;
    background:
      radial-gradient(ellipse 38% 62% at 34% 52%, var(--fur-cream) 0, var(--fur-gold) 55%, rgba(233,196,140,0) 100%),
      radial-gradient(ellipse 27% 70% at 78% 58%, var(--fur-grey) 0, var(--fur-grey-dark) 60%, rgba(185,175,166,0) 100%),
      linear-gradient(90deg, rgba(226,190,140,.55) 0, rgba(215,190,165,.7) 60%, rgba(205,195,185,.4) 100%);
  }
  .account-name { left: 58px; top: 62px; font-size: 22px; font-weight: 700; color: var(--ink-soft); }
  .account-address { left: 58px; top: 85px; font-size: 20px; line-height: 23px; color: var(--ink-soft); }
  .cheque-number { left: 1022px; top: 46px; font-size: 24px; font-weight: 700; }
  .date-label { left: 783px; top: 111px; font-size: 20px; }
  .date-boxes { left: 850px; top: 91px; display: flex; gap: 3px; }
  .date-box { width: 36px; height: 36px; background: var(--field); }
  .date-format { left: 850px; top: 131px; display: flex; gap: 3px; }
  .date-format span { width: 36px; text-align: center; font-size: 14px; }
  .payee-label { left: 57px; top: 191px; font-size: 14px; line-height: 14px; }
  .currency { left: 948px; top: 186px; font-size: 30px; }
  .amount-box { left: 973px; top: 175px; width: 193px; height: 47px; background: var(--field); }
  .dollars { left: 918px; top: 253px; font-size: 15px; }
  .bank-mark { left: 58px; top: 288px; width: 90px; height: 78px; }
  .bank-details { left: 153px; top: 300px; font-size: 19px; line-height: 19px; }
  .company { left: 808px; top: 333px; font-size: 16px; }
  .memo { left: 60px; top: 383px; font-size: 12px; }
  .rules { left: 0; top: 0; }
  .security {
    left: 1160px; top: 270px; width: 32px; height: 136px;
    border: 1px solid var(--line);
    display: flex; flex-direction: column; align-items: center;
  }
  .security-text { writing-mode: vertical-rl; transform: rotate(180deg); font-size: 8px; line-height: 9px; margin-top: 4px; height: 62px; }
  .security-lock { width: 14px; height: 14px; border: 1.5px solid var(--ink); border-radius: 2px; margin-top: 6px; }
  .security-code { font-size: 7px; margin-top: 4px; }
  .security-badge { width: 18px; height: 14px; background: var(--ink); margin-top: 4px; }
  .micr {
    left: 52px; top: 446px; font-family: "Share Tech Mono", monospace;
    font-size: 32px; letter-spacing: 5px; white-space: pre;
  }
</style>
</head>
<body>
<div class="canvas">
  <div class="cheque abs"></div>
  <div class="pet-photo abs" role="img" aria-label="Photo of a golden puppy nuzzling a grey kitten"></div>

  <svg class="rules abs" width="1200" height="544" aria-hidden="true">
    <g stroke="var(--line)" stroke-width="1.2" fill="none">
      <line x1="57" y1="221" x2="921" y2="221"/>
      <line x1="921" y1="221" x2="921" y2="190"/>
      <line x1="59" y1="275" x2="905" y2="275"/>
      <line x1="905" y1="275" x2="913" y2="242"/>
      <line x1="58" y1="397" x2="585" y2="397"/>
      <line x1="687" y1="397" x2="1098" y2="397"/>
    </g>
  </svg>

  <div class="account-name abs">LRTV - Quillmark Cheques Personal Cheque</div>
  <div class="account-address abs">15 Residential Street<br>Toronto, Ontario M1M 1M1</div>
  <div class="cheque-number abs">101</div>

  <div class="date-label abs">DATE</div>
  <div class="date-boxes abs">
    <div class="date-box"></div><div class="date-box"></div><div class="date-box"></div><div class="date-box"></div>
    <div class="date-box"></div><div class="date-box"></div><div class="date-box"></div><div class="date-box"></div>
  </div>
  <div class="date-format abs">
    <span>D</span><span>D</span><span>M</span><span>M</span><span>Y</span><span>Y</span><span>Y</span><span>Y</span>
  </div>

  <div class="payee-label abs">PAY TO THE<br>ORDER OF</div>
  <div class="currency abs">$</div>
  <div class="amount-box abs"></div>
  <div class="dollars abs">100 DOLLARS</div>

  <svg class="bank-mark abs" viewBox="0 0 90 78" aria-hidden="true">
    <circle cx="45" cy="39" r="34" fill="none" stroke="var(--ink)" stroke-width="3"/>
  </svg>
  <div class="bank-details abs"><strong>Your Financial Institution</strong><br>200 Finance Avenue<br>Your City, Your Province A1B 2CS</div>

  <div class="company abs">Optional Company Name</div>
  <div class="memo abs">MEMO</div>

  <div class="security abs">
    <div class="security-text">Details on Back<br>Détails au Verso</div>
    <div class="security-lock"></div>
    <div class="security-code">0603</div>
    <div class="security-badge"></div>
  </div>

  <div class="micr abs">⑈101⑈ ⑆12345⑉678⑆ 12345⑉6789⑈</div>
</div>
</body>
</html>
```